KESTREL HAIR STUDIO NEEDS A FLYER MADE

I’m wanting a flyer made up for a letter box drop for my hair salon.
It needs to target Men and Ladies.
I want to list my services we offer.
I also want on the flyer - (Present this flyer to receive
20% off any hair Colour Service)

Also wanting our logo, phone number and address.

I also want to our regular weekly deals on the back.
I will attach a inspirational picture for the flyer.

Industry/Entity Type

Hairdresser

Font styles to use
Serif
Sans Serif
Script

Requirements
Must have
• I want to list my services we offer
- Mens & Ladies Haircuts
- Style Cuts
- Colour Services
- Blowdry & Styling
- Up Styles
- Perming
- Chemical straightening

I also want on the flyer
Present this flyer to receive
20% off any hair Colour Service

Phone: 47208356
Address: Shop 3/214 Garrow Street, The Lindens, Brennan QLD 4812

I also want to our weekly deals on the back side.
Mens Day Wednesday
$19.00 Haircuts

Thursday Seniors Day
- Shampoo, Ladies Haircut & Blowdry $35
- Ladies Haircut & Blowdry $30
- Shampoo & Blowdry $27.00
-$5off any colour service
- Perm (includes Trim & Blowdry) $85
- Facial Waxing $10

FRIDAY HAPPY HOUR 3PM – 5PM
- Shampoo, Blow dry & Style $40.00
- Shampoo, Mens Haircut & Style $29.00
(Complimentary beverage on arrival)

BOOK NOW

Follow us on facebook
Nice to have
• Photos of our work (hair) we do.

```html
<!DOCTYPE html>
<html lang="en">
<head>
<meta charset="utf-8">
<title>Kestrel Hair Studio – Flyer Front &amp; Back</title>
<link href="https://fonts.googleapis.com/css2?family=Montserrat:wght@400;500;600&family=Roboto+Slab:wght@400;500;700&display=swap" rel="stylesheet">
<style>
  :root{
    --ink:#111111;
    --black:#0a0a0a;
    --white:#ffffff;
    --blush:#f3c9cc;
    --row:#e4e4e4;
    --price:#f6cfd1;
    --stage:#e8e6e3;
    --check:#9a9a9a;
  }
  *{box-sizing:border-box;margin:0;padding:0}
  html,body{width:1200px;height:1200px;overflow:hidden;background:var(--stage)}
  .canvas{position:relative;width:1200px;height:1200px}
  .flyer{position:absolute;top:233px;width:520px;height:735px;background:var(--white);overflow:hidden;box-shadow:0 2px 10px rgba(0,0,0,.18)}
  .flyer--front{left:52px}
  .flyer--back{left:628px}
  .layer{position:absolute;inset:0}
  .shop-photo{position:absolute;left:0;top:0;width:520px;height:360px;
    background:linear-gradient(160deg,#d9d6d4 0%,#b9b2ab 40%,#6f6a62 70%,#3d3a35 100%)}
  .work-photo{position:absolute;border-radius:50%;border:5px solid var(--blush);overflow:hidden}
  .work-photo--cut{background:radial-gradient(circle at 45% 45%,#c9a890 0%,#8a6e5c 45%,#2f2a27 100%)}
  .work-photo--waves{background:radial-gradient(circle at 55% 45%,#b7a08c 0%,#8d7867 50%,#4a403a 100%)}
  .work-photo--blonde{background:radial-gradient(circle at 50% 45%,#efe6d6 0%,#cdbda3 45%,#6b5a48 100%)}
  .work-photo--fade{background:radial-gradient(circle at 50% 40%,#8b6a53 0%,#5c463a 45%,#1f1b19 100%)}

  .brand{position:absolute;font-family:"Montserrat",sans-serif;font-weight:500;color:var(--ink);text-align:center}
  .brand__name{display:block;font-size:33px;letter-spacing:1px;line-height:1}
  .brand__sub{display:block;font-size:10px;letter-spacing:4px;margin-top:6px}

  .services{position:absolute;left:23px;top:420px}
  .services__title{font-family:"Roboto Slab",serif;font-weight:700;font-size:16px;color:var(--ink);letter-spacing:.2px}
  .services__list{list-style:none;margin-top:6px}
  .services__list li{font-family:"Montserrat",sans-serif;font-size:10.5px;color:var(--ink);height:17.5px;line-height:17.5px;display:flex;align-items:center}
  .services__list li svg{margin-right:6px}

  .offer{position:absolute;left:23px;top:586px;font-family:"Roboto Slab",serif;color:var(--ink)}
  .offer__lead{font-size:14px}
  .offer__big{font-size:21px;font-weight:700;line-height:1.1;margin-top:2px}
  .offer__tail{font-size:14px}

  .footer{position:absolute;left:0;right:0;top:698px;display:flex;align-items:center;padding-left:24px;gap:10px;
    font-family:"Montserrat",sans-serif;font-weight:500;font-size:9.6px;color:var(--white);white-space:nowrap}
  .footer__item{display:flex;align-items:center;gap:4px}
  .footer__follow{display:flex;align-items:center;gap:8px;margin-left:6px}
  .footer__dot{width:13px;height:13px;border-radius:50%;background:var(--white)}

  .deals{position:absolute;left:24px;font-family:"Roboto Slab",serif;color:var(--ink)}
  .deals__heading{font-size:12px;font-weight:700}
  .deals__heading--sm{font-size:10px}
  .deals__text{font-size:12px}
  .price-table{position:absolute;left:24px;width:279px;border-collapse:separate;border-spacing:0 2px;font-family:"Roboto Slab",serif;color:#222}
  .price-table td{background:var(--row);font-size:10.5px;height:15.5px;padding:0 6px}
  .price-table td.price-table__price{background:var(--price);width:40px;text-align:center;font-size:9.5px;font-weight:500;border-left:4px solid var(--white)}
  .price-table--happy td{font-size:8.4px;height:18px}
  .price-table--happy tr.tall td{height:26px;line-height:1.2}
  .book-now{position:absolute;left:343px;top:583px;font-family:"Roboto Slab",serif;font-weight:700;font-size:27px;color:var(--ink);letter-spacing:.3px}
</style>
</head>
<body>
<main class="canvas">

  <!-- FRONT -->
  <section class="flyer flyer--front">
    <div class="shop-photo" role="img" aria-label="Salon shopfront window with white bistro table, chairs, flowers and a fiddle-leaf plant"></div>
    <svg class="layer" width="520" height="735" viewBox="0 0 520 735" aria-hidden="true">
      <path d="M0,370 L0,336 C120,290 320,296 520,250 L520,370 Z" fill="var(--black)"/>
      <path d="M0,735 L0,356 C130,314 320,318 520,272 L520,735 Z" fill="var(--white)"/>
      <path d="M0,356 C130,314 320,318 520,272" fill="none" stroke="var(--blush)" stroke-width="4"/>
      <path d="M0,735 L0,658 C160,678 340,660 520,598 L520,735 Z" fill="var(--black)"/>
      <path d="M0,652 C160,672 340,654 520,592" fill="none" stroke="var(--blush)" stroke-width="4"/>
    </svg>
    <div class="work-photo work-photo--waves" style="left:360px;top:243px;width:200px;height:200px" role="img" aria-label="Client with long soft blonde-brown waves"></div>
    <div class="work-photo work-photo--cut" style="left:224px;top:310px;width:186px;height:186px" role="img" aria-label="Men's short tapered haircut, side view"></div>
    <div class="work-photo work-photo--fade" style="left:315px;top:448px;width:216px;height:216px" role="img" aria-label="Men's textured crop haircut, back view"></div>

    <div class="brand" style="left:22px;top:358px;width:216px">
      <span class="brand__name">KESTREL</span>
      <span class="brand__sub">HAIR-STUDIO</span>
    </div>

    <div class="services">
      <h2 class="services__title">OUR SERVICES OFFER</h2>
      <ul class="services__list">
        <li><svg width="8" height="8" viewBox="0 0 8 8"><circle cx="4" cy="4" r="4" fill="var(--check)"/><path d="M2.2,4.1 3.5,5.3 5.9,2.8" stroke="#fff" stroke-width="1" fill="none"/></svg>Mens &amp; Ladies Haircuts</li>
        <li><svg width="8" height="8" viewBox="0 0 8 8"><circle cx="4" cy="4" r="4" fill="var(--check)"/><path d="M2.2,4.1 3.5,5.3 5.9,2.8" stroke="#fff" stroke-width="1" fill="none"/></svg>Style Cuts</li>
        <li><svg width="8" height="8" viewBox="0 0 8 8"><circle cx="4" cy="4" r="4" fill="var(--check)"/><path d="M2.2,4.1 3.5,5.3 5.9,2.8" stroke="#fff" stroke-width="1" fill="none"/></svg>Colour Services</li>
        <li><svg width="8" height="8" viewBox="0 0 8 8"><circle cx="4" cy="4" r="4" fill="var(--check)"/><path d="M2.2,4.1 3.5,5.3 5.9,2.8" stroke="#fff" stroke-width="1" fill="none"/></svg>Blowdry &amp; Styling</li>
        <li><svg width="8" height="8" viewBox="0 0 8 8"><circle cx="4" cy="4" r="4" fill="var(--check)"/><path d="M2.2,4.1 3.5,5.3 5.9,2.8" stroke="#fff" stroke-width="1" fill="none"/></svg>Up Styles</li>
        <li><svg width="8" height="8" viewBox="0 0 8 8"><circle cx="4" cy="4" r="4" fill="var(--check)"/><path d="M2.2,4.1 3.5,5.3 5.9,2.8" stroke="#fff" stroke-width="1" fill="none"/></svg>Perming</li>
        <li><svg width="8" height="8" viewBox="0 0 8 8"><circle cx="4" cy="4" r="4" fill="var(--check)"/><path d="M2.2,4.1 3.5,5.3 5.9,2.8" stroke="#fff" stroke-width="1" fill="none"/></svg>Chemical straightening</li>
      </ul>
    </div>

    <div class="offer">
      <p class="offer__lead">Present this flyer to receive</p>
      <p class="offer__big">20% OFF</p>
      <p class="offer__tail">any hair Colour Service</p>
    </div>

    <footer class="footer">
      <span class="footer__item"><svg width="14" height="14" viewBox="0 0 14 14"><circle cx="7" cy="7" r="6.3" fill="none" stroke="#fff" stroke-width="1"/><path d="M4.6,3.8 5.8,3.6 6.4,5.2 5.6,5.9 C6,6.9 7,7.9 8,8.3 L8.7,7.5 10.3,8.1 10.1,9.3 C8,9.8 4.2,6 4.6,3.8Z" fill="#fff"/></svg>472 083 56</span>
      <span class="footer__item"><svg width="14" height="14" viewBox="0 0 14 14"><circle cx="7" cy="7" r="6.3" fill="none" stroke="#fff" stroke-width="1"/><path d="M7,3.3 C5.5,3.3 4.6,4.4 4.6,5.6 C4.6,7.3 7,10.3 7,10.3 C7,10.3 9.4,7.3 9.4,5.6 C9.4,4.4 8.5,3.3 7,3.3Z" fill="#fff"/><circle cx="7" cy="5.6" r="1" fill="#000"/></svg>Shop 3/214 Garrow Street, The Lindens, Brennan QLD 4812</span>
      <span class="footer__follow">Follow us <span class="footer__dot"></span></span>
    </footer>
  </section>

  <!-- BACK -->
  <section class="flyer flyer--back">
    <div class="shop-photo" style="height:300px" role="img" aria-label="Salon shopfront window with white bistro table, chairs, flowers and a fiddle-leaf plant"></div>
    <svg class="layer" width="520" height="735" viewBox="0 0 520 735" aria-hidden="true">
      <path d="M0,320 L0,278 C140,310 330,300 520,200 L520,320 Z" fill="var(--black)"/>
      <path d="M0,735 L0,312 C140,332 330,322 520,222 L520,735 Z" fill="var(--white)"/>
      <path d="M0,312 C140,332 330,322 520,222" fill="none" stroke="var(--blush)" stroke-width="4"/>
      <path d="M0,735 L0,668 C170,684 360,650 520,628 L520,735 Z" fill="var(--black)"/>
      <path d="M0,662 C170,678 360,644 520,622" fill="none" stroke="var(--blush)" stroke-width="4"/>
    </svg>
    <div class="work-photo work-photo--waves" style="left:388px;top:200px;width:168px;height:168px" role="img" aria-label="Client with long brunette curled waves"></div>
    <div class="work-photo work-photo--blonde" style="left:288px;top:256px;width:140px;height:140px" role="img" aria-label="Client with sleek platinum blonde hair, back view"></div>
    <div class="work-photo work-photo--fade" style="left:343px;top:362px;width:180px;height:180px" role="img" aria-label="Men's skin fade with textured top, back view"></div>

    <div class="brand" style="left:22px;top:362px;width:216px">
      <span class="brand__name">KESTREL</span>
      <span class="brand__sub">HAIR-STUDIO</span>
    </div>

    <div class="deals" style="top:428px">
      <p class="deals__heading">Mens Day Wednesday</p>
      <p class="deals__text">$19.00 Haircuts</p>
    </div>
    <div class="deals" style="top:467px">
      <p class="deals__heading deals__heading--sm">Thursday Seniors Day</p>
    </div>
    <table class="price-table" style="top:481px">
      <tr><td>Shampoo, Ladies Haircut &amp; Blowdry</td><td class="price-table__price">$35</td></tr>
      <tr><td>Ladies Haircut &amp; Blowdry</td><td class="price-table__price">$30</td></tr>
      <tr><td>Shampoo &amp; Blowdry</td><td class="price-table__price">$27</td></tr>
      <tr><td>Perm (includes Trim &amp; Blowdry)</td><td class="price-table__price">$85</td></tr>
      <tr><td>Facial Waxing</td><td class="price-table__price">$10</td></tr>
    </table>

    <div class="deals" style="top:583px">
      <p class="deals__heading deals__heading--sm">FRIDAY HAPPY HOUR 3PM – 5PM</p>
    </div>
    <table class="price-table price-table--happy" style="top:596px">
      <tr><td>Shampoo, Blow dry &amp; Style</td><td class="price-table__price">$40</td></tr>
      <tr class="tall"><td>Shampoo, Mens Haircut &amp; Style<br>(Complimentary beverage on arrival)</td><td class="price-table__price">$29</td></tr>
    </table>

    <p class="book-now">BOOK NOW</p>

    <footer class="footer">
      <span class="footer__item"><svg width="14" height="14" viewBox="0 0 14 14"><circle cx="7" cy="7" r="6.3" fill="none" stroke="#fff" stroke-width="1"/><path d="M4.6,3.8 5.8,3.6 6.4,5.2 5.6,5.9 C6,6.9 7,7.9 8,8.3 L8.7,7.5 10.3,8.1 10.1,9.3 C8,9.8 4.2,6 4.6,3.8Z" fill="#fff"/></svg>472 083 56</span>
      <span class="footer__item"><svg width="14" height="14" viewBox="0 0 14 14"><circle cx="7" cy="7" r="6.3" fill="none" stroke="#fff" stroke-width="1"/><path d="M7,3.3 C5.5,3.3 4.6,4.4 4.6,5.6 C4.6,7.3 7,10.3 7,10.3 C7,10.3 9.4,7.3 9.4,5.6 C9.4,4.4 8.5,3.3 7,3.3Z" fill="#fff"/><circle cx="7" cy="5.6" r="1" fill="#000"/></svg>Shop 3/214 Garrow Street, The Lindens, Brennan QLD 4812</span>
      <span class="footer__follow">Follow us <span class="footer__dot"></span></span>
    </footer>
  </section>

</main>
</body>
</html>
```